Brookvale Building Company - advertisement poster

I am looking to print some canvas signs to advertise my general contracting company, Brookvale Building Company. The sign will measure 6' long x 3' high so the size should match that ratio. I already have a logo icon, which is the Letter 'B' and some trees that I would like to incorporate, see attached. I would also like the to have the following information listed:
1) phone number: 831-555-0172
2) email: brookvalebuildingcompany@mailnest.example
3) website: brookvalebuildingcompany.example
4) Lic#4826130
5) I want to use this text: "BUILD WITH THE B-CREW!"

The ad should be relatively simple and clean. Black and Green are my company colors. I am open to creative ideas!

Target Market(s)

People looking to renovate their homes

Industry/Entity Type

Construction

Colors
59FF00
82FF00
B8FF75
E3FFCB
F4FFEA

Requirements
Must have
• Must have my company logo
Should not have
• No photos or complex graphics

```html
<!DOCTYPE html>
<html lang="en">
<head>
<meta charset="utf-8">
<title>Brookvale Building Company – Sign</title>
<link rel="stylesheet" href="https://fonts.googleapis.com/css2?family=Archivo+Black&family=Montserrat:wght@600;700;800&display=swap">
<style>
  :root {
    --backdrop: #6f6f6f;
    --paper: #ffffff;
    --navy: #161e63;
    --green: #6cb33f;
    --ink: #1b1b22;
    --tab: #eef6fb;
  }
  * { margin: 0; padding: 0; box-sizing: border-box; }
  html, body { width: 1200px; height: 701px; overflow: hidden; }
  body { background: var(--backdrop); position: relative; font-family: "Montserrat", sans-serif; }

  .sign {
    position: absolute; left: 64px; top: 82px; width: 1073px; height: 536px;
    background: var(--paper); overflow: hidden;
    box-shadow: 0 4px 14px rgba(0,0,0,.35);
  }
  .headline {
    position: absolute; left: 0; width: 100%; text-align: center;
    font-family: "Archivo Black", sans-serif; line-height: 1; white-space: nowrap;
  }
  .headline--main { top: 10px; font-size: 166px; color: var(--navy); letter-spacing: 1px; }
  .headline--sub { top: 150px; font-size: 92px; color: var(--green); letter-spacing: -1px; }

  .phone-band {
    position: absolute; left: 0; top: 244px; width: 100%; height: 148px; background: var(--navy);
  }
  .phone {
    position: absolute; left: 0; top: 4px; width: 100%; padding-left: 18px; text-align: center;
    font-weight: 800; font-size: 104px; color: var(--paper); letter-spacing: 3px; line-height: 1.2;
  }
  .license-tab { position: absolute; left: 448px; top: 344px; width: 416px; height: 58px; }
  .license {
    position: absolute; left: 0; top: 0; width: 100%; height: 100%;
    display: flex; align-items: center; justify-content: center;
    font-weight: 700; font-size: 34px; color: var(--ink);
  }

  .email {
    position: absolute; left: 372px; top: 412px; display: flex; align-items: center; gap: 12px;
    font-weight: 700; font-size: 26px; color: var(--ink); white-space: nowrap;
  }
  .email svg { width: 24px; height: 22px; }

  .web-band { position: absolute; left: 0; top: 454px; width: 1073px; height: 82px; }
  .website {
    position: absolute; left: 396px; top: 454px; height: 82px; display: flex; align-items: center;
    font-weight: 700; font-size: 35px; color: var(--paper); white-space: nowrap;
  }

  .brand {
    position: absolute; left: 48px; top: 420px; display: flex; align-items: center; gap: 14px;
  }
  .brand-mark { width: 44px; height: 44px; background: var(--green); flex: none; }
  .brand-name {
    font-weight: 800; font-size: 22px; line-height: 1.1; color: var(--navy); text-transform: uppercase;
  }
</style>
</head>
<body>
  <main class="sign">
    <h1 class="headline headline--main">BUILD</h1>
    <p class="headline headline--sub">WITH THE B-CREW!</p>

    <section class="phone-band">
      <p class="phone">831-555-0172</p>
    </section>

    <div class="license-tab">
      <svg width="416" height="58" viewBox="0 0 416 58" aria-hidden="true">
        <polygon points="16,0 400,0 416,58 0,58" fill="var(--tab)"/>
      </svg>
      <p class="license">license #4826130</p>
    </div>

    <p class="email">
      <svg viewBox="0 0 24 22" aria-hidden="true">
        <rect x="1" y="4" width="22" height="17" rx="2" fill="var(--green)"/>
        <polyline points="1,6 12,14 23,6" fill="none" stroke="#fff" stroke-width="2"/>
      </svg>
      brookvalebuildingcompany@mailnest.example
    </p>

    <svg class="web-band" viewBox="0 0 1073 82" aria-hidden="true">
      <polygon points="380,0 1073,0 1073,82 346,82" fill="var(--green)"/>
    </svg>
    <p class="website">brookvalebuildingcompany.example</p>

    <div class="brand">
      <span class="brand-mark"></span>
      <p class="brand-name">Brookvale<br>Building Company</p>
    </div>
  </main>
</body>
</html>
```